Mark Tolvane actor business cards

I need unique and interesting business cards that have my headshot photo, my name, tagline/position/skills, contact info, preferred pronouns (he, him, his), and social media handles. These need to be memorable networking tools to hand out at events that stand out. I am an actor that works in theatre, film, and TV and usually play darker dramatic roles, though it doesn't have to necessarily need to be reflected in the design, but I am not a light, comedic actor. In my email tagline, My position/skills are "Actor, storyteller, theatre maker."

Target Market(s)

Casting directors, film and television community, theatre community.

Industry/Entity Type

Performing Art

Contact Information for Business Card

Mark Tolvane. Pronouns: he, him, his. Contact info: (555)-318-7064, Marktolvane.example, marktolvane@postbox.example. Talent representation: Kirwood Talent Agency. Social Media: Facebook page, twitter and instagram: @MarkTolvanePlays. Company Member of Harbin Theatre Company.

Font styles to use
Serif
Decorative

Colors

Designer to choose colors to be used in the design.

Requirements
Must have
• Headshot photo, name, tagline, preferred pronouns, contact info, Social media handle, talent agency logo, harbin theatre company logo. Both logos should be smaller than my name. Under or near Harbin logo, it should say "Company Member"
Nice to have
• I would like to have the photo, my name, tagline, and maybe pronouns on one side, and all contact info, and social media, and talent agency logo on the other. I would like the style to reflect my type which is a little more serious and somewhat darker, and definitely not comedic.
Should not have
• No extraneous theatre lights, camera, or film, etc. clip art or photos. Use solid backgrounds or photos provided.

```html
<!DOCTYPE html>
<html lang="en">
<head>
<meta charset="utf-8">
<title>Mark Tolvane – Business Cards</title>
<link rel="stylesheet" href="https://fonts.googleapis.com/css2?family=Courgette&family=Open+Sans:wght@400;700&display=swap">
<style>
  :root {
    --backdrop: #2a2a2a;
    --sky: #3db4ea;
    --sky-deep: #1ea3df;
    --paper: #ffffff;
    --ink: #1c1c1c;
    --ink-soft: #555555;
    --photo-top: #6d7f8f;
    --photo-bottom: #3f5a86;
  }
  * { box-sizing: border-box; margin: 0; padding: 0; }
  html, body { width: 1200px; height: 1082px; overflow: hidden; }
  body {
    background: var(--backdrop);
    display: flex;
    justify-content: center;
    align-items: center;
    gap: 60px;
    font-family: "Open Sans", sans-serif;
  }
  .card {
    position: relative;
    width: 440px;
    height: 770px;
    overflow: hidden;
  }

  /* Front */
  .card-front { background: var(--paper); }
  .front-field {
    position: absolute;
    inset: 0 0 100px 0;
    background: var(--sky);
  }
  .agency-mark {
    position: absolute;
    top: 150px;
    left: 60px;
    font-family: "Courgette", cursive;
    color: var(--paper);
    line-height: 1.1;
  }
  .agency-name { font-size: 64px; display: block; }
  .agency-sub { font-size: 20px; display: block; text-align: right; }
  .identity {
    position: absolute;
    top: 370px;
    right: 40px;
    text-align: right;
    color: var(--paper);
  }
  .person-name {
    font-family: "Courgette", cursive;
    font-weight: 400;
    font-size: 34px;
    line-height: 1.1;
  }
  .person-role {
    font-family: "Courgette", cursive;
    font-size: 18px;
    margin-top: 4px;
  }
  .pronouns {
    font-size: 14px;
    margin-top: 2px;
  }
  .contact {
    margin-top: 16px;
    font-size: 15px;
    line-height: 1.45;
  }
  .social-row {
    display: flex;
    justify-content: flex-end;
    align-items: center;
    gap: 8px;
    margin-top: 14px;
  }
  .social-handle {
    font-size: 15px;
    margin-right: 4px;
  }
  .social-dot {
    width: 34px;
    height: 34px;
    border-radius: 50%;
    background: var(--paper);
  }
  .representation {
    position: absolute;
    left: 0; right: 0; bottom: 0;
    height: 100px;
    padding: 26px 40px 0 0;
    text-align: right;
    color: var(--sky-deep);
  }
  .rep-label { font-weight: 700; font-size: 17px; letter-spacing: 0.5px; }
  .rep-agency { font-size: 15px; }

  /* Back */
  .card-back { background: var(--paper); }
  .back-mark {
    position: absolute;
    top: 150px;
    left: 0; right: 0;
    text-align: center;
    font-family: "Courgette", cursive;
    color: var(--ink);
    line-height: 1.1;
  }
  .back-mark .agency-sub { text-align: center; padding-left: 150px; }
  .headshot {
    position: absolute;
    top: 400px;
    left: 95px;
    width: 250px;
    height: 240px;
    border-radius: 14px;
    background: linear-gradient(180deg, var(--photo-top), var(--photo-bottom));
  }
  .company {
    position: absolute;
    top: 665px;
    left: 0; right: 0;
    text-align: center;
    color: var(--ink);
  }
  .company-name {
    display: inline-flex;
    align-items: center;
    gap: 8px;
    font-family: "Courgette", cursive;
    font-size: 20px;
  }
  .company-square {
    width: 14px;
    height: 14px;
    background: var(--sky-deep);
  }
  .company-role {
    font-size: 13px;
    letter-spacing: 1px;
    color: var(--ink-soft);
    margin-top: 2px;
  }
</style>
</head>
<body>
  <section class="card card-front">
    <div class="front-field" role="img" aria-label="Sky blue background with a soft tone-on-tone damask pattern"></div>
    <div class="agency-mark">
      <span class="agency-name">Kirwood</span>
      <span class="agency-sub">Talent Agency</span>
    </div>
    <div class="identity">
      <h1 class="person-name">Mark Tolvane</h1>
      <p class="person-role">Actor, storyteller, theatre maker</p>
      <p class="pronouns">he / him / his</p>
      <p class="contact">
        Phone: (555)-318-7064<br>
        Email: marktolvane@postbox.example<br>
        Web: Marktolvane.example
      </p>
      <div class="social-row">
        <span class="social-handle">@MarkTolvanePlays</span>
        <span class="social-dot"></span>
        <span class="social-dot"></span>
        <span class="social-dot"></span>
      </div>
    </div>
    <div class="representation">
      <p class="rep-label">TALENT REPRESENTATION</p>
      <p class="rep-agency">Kirwood Talent Agency.</p>
    </div>
  </section>

  <section class="card card-back">
    <div class="back-mark">
      <span class="agency-name">Kirwood</span>
      <span class="agency-sub">Talent Agency</span>
    </div>
    <div class="headshot" role="img" aria-label="Headshot photo of Mark Tolvane in a blue shirt"></div>
    <div class="company">
      <p class="company-name"><span class="company-square"></span>Harbin Theatre Company</p>
      <p class="company-role">COMPANY MEMBER</p>
    </div>
  </section>
</body>
</html>
```